Market place for used airplanes/helicopters/parts

http://www.vingtorget.se needs a facelift.

# What is it
Classifieds for used airplanes/helicopters/parts/spare parts/aviation literature, for people in Scandinavia. The number of classifieds is ~120-200. They are mainly in Swedish, English, Norwegian.

It's not a glamorous or luxurious business, but more for people with a genuine interest in flying, technical things.

Similar to sites like this, but they have much more classifieds than my site
http://www.skyvendor.com/list/list.aspx?ETID=1&setype=1&catid=6
http://www.lindqvistflyg.com/planes.asp?meny=1&typ=single
https://www.hangarhub.com/cat.php?mode=listing&main=

# What I want
Design only - no code. I want a modern, maybe a bit bootstrap like, clean, simple, not flashy, web design. I want the design to be in English.

# Audience of the website
Aviation interested men, 45-65 years old, in the nordic countries (around Sweden).

# Logotype that could be used (but not necessarily)
http://www.vingtorget.se/flygplan_till_salu_large.jpg
http://www.vingtorget.se/flygplan_till_salu.eps

Reason: I decided to extend the deadline with 1 day. The reason is that I (unfortunately) managed to put the contest in the wrong category for 1 day + I want to give you all feedback (been too busy the whole day, sorry).

Hi all! 

Thanks everyone for the contributions you made. 

I will setup a poll for the designs that I like most. Will get back when I have more information. 

Thanks and have a nice weekend!
Erik

Target Market(s)

45-65 old Scandinavian men

Industry/Entity Type

Business

Requirements
Must have
• - A list with classifieds on the first page, so the visitor easily can see new classifieds.
- A classifieds should be able to have more than one photo
- A simple navigation for showing classifieds from categories like airplanes, helicopters/gyrocopters, parts, literature, misc (maybe other categories) .... but still, it's just 100-200 ads so it's not needed that much filtration.

- A placeholder/way of showing aviation news/clips. In the old design I had, it was a column to the right. It's enough to show maybe 2-5 placeholders.
- A placeholder for PlaceMint ads somewhere on the site.
Should not have
• - Carousels
- Too much clutter

```html
<!DOCTYPE html>
<html lang="en">
<head>
<meta charset="utf-8">
<title>Vingtorget – Aircraft for Sale</title>
<link href="https://fonts.googleapis.com/css2?family=Arimo:wght@400;700&display=swap" rel="stylesheet">
<style>
:root{
  --blue:#0f63b5;
  --blue-dark:#0b4f93;
  --blue-text:#10509a;
  --cyan:#14a3e0;
  --red:#d9262c;
  --page:#e5e6e8;
  --text:#555;
  --footer:#1d1d1e;
}
*{box-sizing:border-box;margin:0;padding:0}
html,body{width:782px;height:1200px;overflow:hidden}
body{position:relative;background:var(--page);font-family:Arimo,Arial,sans-serif;color:var(--text)}
.abs{position:absolute}

.top-rule{left:0;top:0;width:782px;height:2px;background:var(--cyan)}
.header{left:0;top:2px;width:782px;height:54px;background:#fff}
.brand{left:132px;top:22px;display:flex;align-items:center;gap:6px;font-size:20px;color:var(--blue);letter-spacing:-.3px}
.brand-mark{width:10px;height:10px;background:var(--blue);border-radius:50%}
.search{left:434px;top:18px;width:108px;height:20px;border:1px solid #d4d6d9;font-size:6px;color:#888;padding:6px 0 0 12px}
.search svg{position:absolute;right:7px;top:5px}
.mobile{left:553px;top:21px}
.account{left:576px;top:22px;font-size:7.5px;font-weight:700;color:var(--blue);display:flex;gap:5px}

.nav{left:0;top:56px;width:782px;height:35px;background:linear-gradient(#1c72c4,#0c4f96);border-top:1px solid #0a3f78}
.nav ul{position:absolute;left:148px;top:0;display:flex;list-style:none;height:34px}
.nav li{font-size:7.5px;color:#fff;padding:13px 8px 0;height:34px}
.nav li.active{background:var(--cyan);padding:13px 5px 0}
.upload{left:480px;top:61px;width:58px;height:24px;background:var(--red);border-radius:2px;color:#fff;font-size:7.5px;text-align:center;padding-top:8px}
.socials{left:556px;top:63px;display:flex;gap:3px}
.socials span{width:18px;height:20px;border-radius:3px;display:block}

.intro-title{left:0;top:118px;width:782px;text-align:center;font-size:13.5px;color:var(--blue-text);font-weight:400}
.intro-text{left:152px;top:141px;width:478px;text-align:center;font-size:6px;line-height:7.6px;color:#666}
.intro-rule{left:133px;top:182px;width:522px;height:2px;background:#cfd2d6}

.card{width:160px;height:210px;background:#fff;border-top:3px solid var(--blue-dark);box-shadow:0 8px 6px -5px rgba(0,0,0,.35)}
.photos{display:grid;grid-template-columns:97px 58px;grid-template-rows:48px 48px;gap:2px;padding:3px 0 0 3px}
.photos .main{grid-row:span 2}
.card h3{font-size:9.6px;font-weight:700;color:var(--blue-text);text-align:center;height:24px;padding-top:11px;border-bottom:1px solid #e2e2e2;white-space:nowrap}
.card .desc{font-size:6px;line-height:7.4px;text-align:center;padding:6px 8px 0;height:38px;border-bottom:1px solid #e2e2e2}
.desc b{color:var(--blue);font-weight:400}
.contact{display:flex;gap:8px;padding:5px 0 0 7px}
.avatar{width:32px;height:30px;border:1px solid #d0d0d0;background:linear-gradient(#eef2f7,#c9d6e6)}
.details{font-size:6px;line-height:10px;color:#555;border-left:1px solid #e2e2e2;padding-left:5px}
.details .name{color:var(--blue)}
.details svg{vertical-align:-1px;margin-right:4px}

.ph-red{background:linear-gradient(135deg,#b9c4cf,#c8423a 55%,#6c5a4e)}
.ph-yellowred{background:linear-gradient(160deg,#8a9c78,#d43a2b 50%,#5f6a48)}
.ph-green{background:linear-gradient(170deg,#c9d6e4,#6f9a44 55%,#4c7a2e)}
.ph-gyro{background:linear-gradient(150deg,#5c6a3c,#d7d22b 50%,#3a3f2c)}
.ph-white{background:linear-gradient(170deg,#8fa1b6,#dfe5ec 50%,#5b6655)}
.ph-orange{background:linear-gradient(170deg,#6a9ad2,#e08a2e 55%,#5b7b3a)}
.ph-hangar{background:linear-gradient(170deg,#4a2a1c,#c77b4e 55%,#b99c7a)}
.ph-jet{background:linear-gradient(170deg,#2a2a2d,#e9eaec 50%,#2d2d30)}
.ph-grey{background:linear-gradient(170deg,#c1c9d2,#e4e6e8 50%,#6d7378)}
.ph-engine{background:linear-gradient(135deg,#c3c3bb,#5e5d55 60%,#8a897f)}
.ph-gauge{background:linear-gradient(135deg,#40444a,#a8adb3 50%,#2d3035)}
.ph-blue{background:linear-gradient(135deg,#4d92b3,#8fc3d8 60%,#2f6d8a)}
.ph-seat{background:linear-gradient(135deg,#7a0f12,#d2262c 60%,#8b1418)}
.ph-boxes{background:linear-gradient(135deg,#8c7352,#d9c29a 60%,#6a5a44)}

.news-title{left:130px;top:956px;font-size:13px;color:var(--blue-text);font-weight:400}
.news-nav{left:294px;top:960px;display:flex;gap:3px}
.news-nav span{width:14px;height:12px;border:1px solid #bbb;background:#f4f4f4;font-size:7px;text-align:center;line-height:10px;color:#777}
.news{left:131px;top:975px;width:193px;height:138px;background:#fff;border:1px solid #d4d6d9}
.news-item{height:43px;padding:7px 9px 0 9px;border-bottom:1px solid #e3e3e3;font-size:6px;line-height:7.4px;color:#555}
.news-item:last-child{border:0}
.news-item .more{text-align:right;color:var(--blue)}
.flyer{left:342px;top:960px;width:117px;height:152px;background:linear-gradient(160deg,#6fc4e8,#f2ea7d 45%,#f6f1c4 80%,#c9d7b2);border:3px solid #fff}
.ads{left:475px;top:962px;width:178px;height:148px;background:#fff;border:2px solid #d8d8d8;padding:5px 10px 0;font-size:7.6px;line-height:8.6px;color:#222}
.ad{margin-bottom:10px}
.ad a{color:#1a1acc;font-weight:700;text-decoration:underline}
.ad small{display:block;font-size:5px;color:#1c7c2c}
.ads-foot{position:absolute;left:2px;right:2px;bottom:2px;display:flex;justify-content:space-between;font-size:5.6px}
.ads-foot .by{background:#1c1c1c;color:#fff;padding:1px 4px;border-radius:5px 0 0 0}

.footer-rule{left:0;top:1118px;width:782px;height:5px;background:var(--blue-dark)}
.footer{left:0;top:1123px;width:782px;height:77px;background:var(--footer)}
.footer-links{left:131px;top:1141px;font-size:6.4px;line-height:12.5px;color:#eee}
.footer-social{left:568px;top:1141px;display:flex;gap:7px}
.footer-social span{width:24px;height:24px;display:block;border-radius:2px}
</style>
</head>
<body>
<div class="abs top-rule"></div>
<header class="abs header"></header>
<div class="abs brand"><span class="brand-mark"></span>Vingtorget</div>
<div class="abs search">Search
  <svg width="8" height="8" viewBox="0 0 8 8"><circle cx="3.3" cy="3.3" r="2.5" fill="none" stroke="#999" stroke-width="1"/><path d="M5.2 5.2L7.5 7.5" stroke="#999"/></svg>
</div>
<svg class="abs mobile" width="7" height="12" viewBox="0 0 7 12"><rect x=".5" y=".5" width="6" height="11" rx="1" fill="none" stroke="#1a5aa0"/><rect x="1.5" y="2" width="4" height="7" fill="#1a5aa0"/></svg>
<div class="abs account"><span>Login</span><span style="color:#aaa;font-weight:400">|</span><span>Register</span></div>

<nav class="abs nav">
  <ul>
    <li class="active">Airplanes</li><li>helocopters</li><li>Parts</li><li>Literature</li><li>MISC</li><li>Search</li><li>Support</li>
  </ul>
</nav>
<div class="abs upload">Upload</div>
<div class="abs socials" aria-label="Social links">
  <span style="background:#4db3e6"></span><span style="background:#3a5a98"></span><span style="background:#c4302b"></span><span style="background:#5a8ed0"></span><span style="background:#f28c1e"></span>
</div>

<h1 class="abs intro-title">Aircraft for Sale - the largest market for flights</h1>
<p class="abs intro-text">Lorem ipsum dolor sit amet, consectetur adipisicing elit, sed do eiusmod tempor incididunt ut labore et dolore magna aliqua. Ut...Lorem ipsum dolor sit amet, consectetur adipisicing elit, sed do eiusmod tempor incididunt ut labore et dolore magna aliqua. Ut... Lorem ipsum dolor sit amet, consectetur adipisicing elit, sed do eiusmod tempor incididunt ut labore et dolore magna aliqua. Ut...Lorem ipsum dolor sit amet, consectetur adipisicing elit, sed do eiusmod tempor incididunt ut labore et dolore magna aliqua. Ut...</p>
<div class="abs intro-rule"></div>

<article class="abs card" style="left:132px;top:212px">
  <div class="photos"><div class="main ph-red" role="img" aria-label="Red and white ultralight on a runway"></div><div class="ph-engine" role="img" aria-label="Engine component"></div><div class="ph-engine" role="img" aria-label="Engine"></div></div>
  <h3>Dynavia MR ULC</h3>
  <p class="desc">Lorem ipsum dolor sit amet, consectetur adipisicing elit, sed do eiusmod tempor incididunt ut labore et dolore magna aliqua. Ut... <b>More</b></p>
  <div class="contact"><div class="avatar" role="img" aria-label="Seller avatar"></div><div class="details"><div class="name">Lars Holmqvist</div><div><svg width="7" height="5"><rect x=".5" y=".5" width="6" height="4" fill="none" stroke="#666"/><path d="M.5 .5l3 2.3 3-2.3" fill="none" stroke="#666"/></svg>lars.holmqvist@nordmail.net</div><div><svg width="7" height="6"><rect x=".5" y="1" width="6" height="4.5" rx="1" fill="none" stroke="#666"/><rect x="2" y="2.5" width="3" height="1.5" fill="#666"/></svg>+46-700-11 22 33</div></div></div>
</article>
<article class="abs card" style="left:315px;top:212px">
  <div class="photos"><div class="main ph-yellowred" role="img" aria-label="Red and yellow aerobatic plane on grass"></div><div class="ph-gauge" role="img" aria-label="Instrument panel"></div><div class="ph-engine" role="img" aria-label="Engine"></div></div>
  <h3>Aerobatic Ranger T-7C LN-VTG</h3>
  <p class="desc">Lorem ipsum dolor sit amet, consectetur adipisicing elit, sed do eiusmod tempor incididunt ut labore et dolore magna aliqua. Ut... <b>More</b></p>
  <div class="contact"><div class="avatar" role="img" aria-label="Seller avatar"></div><div class="details"><div class="name">Arne Solberg</div><div><svg width="7" height="5"><rect x=".5" y=".5" width="6" height="4" fill="none" stroke="#666"/><path d="M.5 .5l3 2.3 3-2.3" fill="none" stroke="#666"/></svg>lars.holmqvist@nordmail.net</div><div><svg width="7" height="6"><rect x=".5" y="1" width="6" height="4.5" rx="1" fill="none" stroke="#666"/><rect x="2" y="2.5" width="3" height="1.5" fill="#666"/></svg>+46-700-11 22 33</div></div></div>
</article>
<article class="abs card" style="left:496px;top:212px">
  <div class="photos"><div class="main ph-green" role="img" aria-label="Green aircraft on a grass field"></div><div class="ph-gauge" role="img" aria-label="Cockpit gauge"></div><div class="ph-engine" role="img" aria-label="Engine"></div></div>
  <h3>Pioneer Corvid 160 Auto STC</h3>
  <p class="desc">Lorem ipsum dolor sit amet, consectetur adipisicing elit, sed do eiusmod tempor incididunt ut labore et dolore magna aliqua. Ut... <b>More</b></p>
  <div class="contact"><div class="avatar" role="img" aria-label="Seller avatar"></div><div class="details"><div class="name">Lars Holmqvist</div><div><svg width="7" height="5"><rect x=".5" y=".5" width="6" height="4" fill="none" stroke="#666"/><path d="M.5 .5l3 2.3 3-2.3" fill="none" stroke="#666"/></svg>lars.holmqvist@nordmail.net</div><div><svg width="7" height="6"><rect x=".5" y="1" width="6" height="4.5" rx="1" fill="none" stroke="#666"/><rect x="2" y="2.5" width="3" height="1.5" fill="#666"/></svg>+46-700-11 22 33</div></div></div>
</article>

<article class="abs card" style="left:132px;top:468px">
  <div class="photos"><div class="main ph-gyro" role="img" aria-label="Yellow gyrocopter with two pilots"></div><div class="ph-grey" role="img" aria-label="Control part"></div><div class="ph-grey" role="img" aria-label="Propeller accessories"></div></div>
  <h3>Propeller to paramotor</h3>
  <p class="desc">Lorem ipsum dolor sit amet, consectetur adipisicing elit, sed do eiusmod tempor incididunt ut labore et dolore magna aliqua. Ut... <b>More</b></p>
  <div class="contact"><div class="avatar" role="img" aria-label="Seller avatar"></div><div class="details"><div class="name">Lars Holmqvist</div><div><svg width="7" height="5"><rect x=".5" y=".5" width="6" height="4" fill="none" stroke="#666"/><path d="M.5 .5l3 2.3 3-2.3" fill="none" stroke="#666"/></svg>lars.holmqvist@nordmail.net</div><div><svg width="7" height="6"><rect x=".5" y="1" width="6" height="4.5" rx="1" fill="none" stroke="#666"/><rect x="2" y="2.5" width="3" height="1.5" fill="#666"/></svg>+46-700-11 22 33</div></div></div>
</article>
<article class="abs card" style="left:315px;top:468px">
  <div class="photos"><div class="main ph-white" role="img" aria-label="White and blue single-engine plane parked"></div><div class="ph-gauge" role="img" aria-label="Instrument panel"></div><div class="ph-grey" role="img" aria-label="Headset"></div></div>
  <h3>Cirrel 260. -73</h3>
  <p class="desc">Lorem ipsum dolor sit amet, consectetur adipisicing elit, sed do eiusmod tempor incididunt ut labore et dolore magna aliqua. Ut... <b>More</b></p>
  <div class="contact"><div class="avatar" role="img" aria-label="Seller avatar"></div><div class="details"><div class="name">Arne Solberg</div><div><svg width="7" height="5"><rect x=".5" y=".5" width="6" height="4" fill="none" stroke="#666"/><path d="M.5 .5l3 2.3 3-2.3" fill="none" stroke="#666"/></svg>lars.holmqvist@nordmail.net</div><div><svg width="7" height="6"><rect x=".5" y="1" width="6" height="4.5" rx="1" fill="none" stroke="#666"/><rect x="2" y="2.5" width="3" height="1.5" fill="#666"/></svg>+46-700-11 22 33</div></div></div>
</article>
<article class="abs card" style="left:496px;top:468px">
  <div class="photos"><div class="main ph-orange" role="img" aria-label="Orange and white high-wing plane"></div><div class="ph-engine" role="img" aria-label="Engine"></div><div class="ph-gauge" role="img" aria-label="Avionics parts"></div></div>
  <h3>Mistral Glide 480</h3>
  <p class="desc">Lorem ipsum dolor sit amet, consectetur adipisicing elit, sed do eiusmod tempor incididunt ut labore et dolore magna aliqua. Ut... <b>More</b></p>
  <div class="contact"><div class="avatar" role="img" aria-label="Seller avatar"></div><div class="details"><div class="name">Lars Holmqvist</div><div><svg width="7" height="5"><rect x=".5" y=".5" width="6" height="4" fill="none" stroke="#666"/><path d="M.5 .5l3 2.3 3-2.3" fill="none" stroke="#666"/></svg>lars.holmqvist@nordmail.net</div><div><svg width="7" height="6"><rect x=".5" y="1" width="6" height="4.5" rx="1" fill="none" stroke="#666"/><rect x="2" y="2.5" width="3" height="1.5" fill="#666"/></svg>+46-700-11 22 33</div></div></div>
</article>

<article class="abs card" style="left:132px;top:724px">
  <div class="photos"><div class="main ph-hangar" role="img" aria-label="Small plane in front of a hangar"></div><div class="ph-blue" role="img" aria-label="Fuselage detail"></div><div class="ph-engine" role="img" aria-label="Engine"></div></div>
  <h3>Life Preserver, AQM model LP-20</h3>
  <p class="desc">Lorem ipsum dolor sit amet, consectetur adipisicing elit, sed do eiusmod tempor incididunt ut labore et dolore magna aliqua. Ut... <b>More</b></p>
  <div class="contact"><div class="avatar" role="img" aria-label="Seller avatar"></div><div class="details"><div class="name">Lars Holmqvist</div><div><svg width="7" height="5"><rect x=".5" y=".5" width="6" height="4" fill="none" stroke="#666"/><path d="M.5 .5l3 2.3 3-2.3" fill="none" stroke="#666"/></svg>lars.holmqvist@nordmail.net</div><div><svg width="7" height="6"><rect x=".5" y="1" width="6" height="4.5" rx="1" fill="none" stroke="#666"/><rect x="2" y="2.5" width="3" height="1.5" fill="#666"/></svg>+46-700-11 22 33</div></div></div>
</article>
<article class="abs card" style="left:315px;top:724px">
  <div class="photos"><div class="main ph-jet" role="img" aria-label="White light aircraft in a hangar"></div><div class="ph-blue" role="img" aria-label="Fuselage detail"></div><div class="ph-seat" role="img" aria-label="Red leather seats"></div></div>
  <h3>ROTEK 640 Ice Injection Engine</h3>
  <p class="desc">Lorem ipsum dolor sit amet, consectetur adipisicing elit, sed do eiusmod tempor incididunt ut labore et dolore magna aliqua. Ut... <b>More</b></p>
  <div class="contact"><div class="avatar" role="img" aria-label="Seller avatar"></div><div class="details"><div class="name">Arne Solberg</div><div><svg width="7" height="5"><rect x=".5" y=".5" width="6" height="4" fill="none" stroke="#666"/><path d="M.5 .5l3 2.3 3-2.3" fill="none" stroke="#666"/></svg>lars.holmqvist@nordmail.net</div><div><svg width="7" height="6"><rect x=".5" y="1" width="6" height="4.5" rx="1" fill="none" stroke="#666"/><rect x="2" y="2.5" width="3" height="1.5" fill="#666"/></svg>+46-700-11 22 33</div></div></div>
</article>
<article class="abs card" style="left:496px;top:724px">
  <div class="photos"><div class="main ph-grey" role="img" aria-label="Low-wing plane on an apron"></div><div class="ph-boxes" role="img" aria-label="Boxed instruments"></div><div class="ph-boxes" role="img" aria-label="Spare parts"></div></div>
  <h3>Kjøp og salg</h3>
  <p class="desc">Lorem ipsum dolor sit amet, consectetur adipisicing elit, sed do eiusmod tempor incididunt ut labore et dolore magna aliqua. Ut... <b>More</b></p>
  <div class="contact"><div class="avatar" role="img" aria-label="Seller avatar"></div><div class="details"><div class="name">Lars Holmqvist</div><div><svg width="7" height="5"><rect x=".5" y=".5" width="6" height="4" fill="none" stroke="#666"/><path d="M.5 .5l3 2.3 3-2.3" fill="none" stroke="#666"/></svg>lars.holmqvist@nordmail.net</div><div><svg width="7" height="6"><rect x=".5" y="1" width="6" height="4.5" rx="1" fill="none" stroke="#666"/><rect x="2" y="2.5" width="3" height="1.5" fill="#666"/></svg>+46-700-11 22 33</div></div></div>
</article>

<h2 class="abs news-title">Latest News</h2>
<div class="abs news-nav"><span>&#8249;</span><span>&#8250;</span></div>
<section class="abs news">
  <div class="news-item">Lorem ipsum dolor sit amet, consectetur adipisicing elit, sed do eiusmod tempor incididunt ut labore et dolore magna aliqua. Ut...Lorem ipsum dolor sit amet, consectetur adipisicing elit,<div class="more">--Read more...</div></div>
  <div class="news-item">Lorem ipsum dolor sit amet, consectetur adipisicing elit, sed do eiusmod tempor incididunt ut labore et dolore magna aliqua. Ut...Lorem ipsum dolor sit amet, consectetur adipisicing elit,<div class="more">--Read more...</div></div>
  <div class="news-item">Lorem ipsum dolor sit amet, consectetur adipisicing elit, sed do eiusmod tempor incididunt ut labore et dolore magna aliqua. Ut...Lorem ipsum dolor sit amet, consectetur adipisicing elit,<div class="more">--Read more...</div></div>
</section>
<div class="abs flyer" role="img" aria-label="Flying club summer fly-in poster for Ekdala Flygklubb"></div>
<aside class="abs ads">
  <div class="ad"><a>How to Make Electricity</a><br>Don't ever pay for electricity, you can make it simple &amp; cheap at home<small>PowerAtHome.example</small></div>
  <div class="ad"><a>Prepare to be Shocked</a><br>Millions have already taken this amazing test. What's your health score?<small>AgeCheck.example</small></div>
  <div class="ad"><a>Make Solar Panel in 1 day</a><br>Make cheap homemade solar panels Cut Power Bill by 99%. $49 Kits<small>SunPanelKits.example</small></div>
  <div class="ads-foot"><span style="color:#999">&#9665;&#9655;</span><span class="by">Ads by PlaceMint</span></div>
</aside>

<div class="abs footer-rule"></div>
<footer class="abs footer"></footer>
<div class="abs footer-links">Home | About Us | Services | Contact Us<br>Copyright NordWings LLC</div>
<div class="abs footer-social" aria-label="Social links">
  <span style="background:#3a5a98"></span><span style="background:#1da1e2"></span><span style="background:#cb2027"></span>
</div>
</body>
</html>
```